Kestrel Finish Studio (KFS)

I would like to design a dedicated site for my KFS product, which allows industry employees to be trained in the visual inspection of mechanical parts. My product is a 3D simulator (see https://morvint-works.ch/our-applications/virtual-reality/ and https://morvint-works.ch for videos) which makes it possible to manufacture standard parts representative of a type of defect which is accepted or refused by the quality department. These master parts can be used to create a common quality culture in the company and to train employees in a homogeneous way. The simulator is initially designed for watchmaking, but must be designed for much broader industries (cars, phone reconditioning, ball bearings, etc.)
L'information que j'ai donnée n'est pas assez précise. Je dois préciser les domaines métiers visés par le site internet. J'ai besoin de quelques jours pour choisir les domaines les plus représentatifs.
Coded - Design and coding required
1 page

```html
<!DOCTYPE html>
<html lang="en">
<head>
<meta charset="utf-8">
<title>Kestrel Finish Studio</title>
<link href="https://fonts.googleapis.com/css2?family=Montserrat:wght@600;700;800&family=Roboto:wght@400;500;700&display=swap" rel="stylesheet">
<style>
:root{
  --navy:#0c1838;
  --navy-2:#14244f;
  --blue:#1668c4;
  --blue-bright:#1e88e5;
  --ink:#1b2233;
  --muted:#6b7280;
  --light:#f2f4f7;
  --line:#d9dde4;
  --white:#ffffff;
  --footer:#151a2e;
}
*{box-sizing:border-box;margin:0;padding:0}
html,body{width:1200px;height:4052px;overflow:hidden}
body{font-family:"Roboto",Arial,sans-serif;color:var(--ink);background:var(--white);position:relative}
h1,h2,h3,h4,.brand{font-family:"Montserrat",Arial,sans-serif}
section,header,footer{position:relative;width:1200px;overflow:hidden}

/* header */
.site-header{height:152px;background:var(--white)}
.brand{position:absolute;left:112px;top:36px;color:var(--navy);font-weight:800;font-size:27px;line-height:32px;letter-spacing:.5px}
.topbar{position:absolute;left:680px;top:0;width:420px;height:40px;background:var(--navy);display:flex;align-items:center;font-size:14px;color:var(--white)}
.topbar .mail{display:flex;align-items:center;gap:8px;padding-left:24px;width:220px}
.topbar .phone{display:flex;align-items:center;gap:8px;height:40px;background:var(--blue);padding:0 18px;flex:1;font-weight:500}
.main-nav{position:absolute;left:432px;top:78px;display:flex;gap:26px;font-size:15px;font-weight:500;color:var(--ink)}
.main-nav a{color:inherit;text-decoration:none}
.main-nav .active{color:var(--blue)}
.social{position:absolute;left:962px;top:72px;display:flex;gap:10px}
.social span{width:34px;height:34px;border-radius:50%;background:var(--blue);display:block}
.social span:nth-child(2),.social span:nth-child(3){background:var(--white);border:2px solid var(--navy)}

/* hero */
.hero{height:548px;background:var(--navy)}
.hero .photo{position:absolute;inset:0;background:linear-gradient(120deg,#2b4f86 0%,#7fa6cf 45%,#c9dcef 70%,#8fb1d6 100%)}
.hero svg.shape{position:absolute;inset:0}
.hero-text{position:absolute;left:112px;top:228px;color:var(--white)}
.hero-text h1{font-size:42px;line-height:50px;font-weight:800}
.hero-text p{margin-top:30px;font-size:19px;line-height:26px;font-weight:500;letter-spacing:.4px}

/* about */
.about{height:580px}
.about .frame{position:absolute;left:140px;top:118px;width:256px;height:226px;background:#0a0f1c;border:8px solid #242c3c}
.about .frame .photo{position:absolute;inset:10px;background:radial-gradient(circle at 60% 60%,#b58a2c 0%,#5a3f12 30%,#0a0d14 65%)}
.about .frame .stand{position:absolute;left:-8px;right:-8px;bottom:-30px;height:22px;background:#2d3545;border-radius:0 0 6px 6px}
.about-copy{position:absolute;left:600px;top:118px;width:490px}
.about-copy h2{font-size:34px;line-height:40px;font-weight:800;color:var(--navy)}
.about-copy p{margin-top:24px;font-size:14px;line-height:22px;color:var(--muted);text-align:justify}
.btn{display:inline-flex;align-items:center;gap:8px;background:var(--blue);color:var(--white);font-size:13px;font-weight:700;letter-spacing:.5px;padding:12px 18px;border-radius:3px}
.about-copy .btn{margin-top:26px}

/* services */
.services{height:600px;background:var(--light)}
.section-title{text-align:center;font-size:36px;font-weight:800;color:var(--navy)}
.section-title::after{content:"";display:block;width:70px;height:4px;background:var(--blue);margin:12px auto 0}
.services .section-title{padding-top:68px}
.service-cards{position:absolute;left:120px;top:176px;width:960px;display:flex;justify-content:space-between}
.service-card{width:280px;height:352px;background:var(--white);border-radius:6px;box-shadow:0 4px 14px rgba(12,24,56,.12);padding:14px;text-align:center;position:relative}
.service-card.featured{border:3px solid var(--blue);width:300px;height:372px;margin-top:-6px}
.service-card .photo{height:178px;border-radius:4px}
.service-card h3{margin-top:20px;font-size:16px;font-weight:700;color:var(--navy)}
.service-card p{margin-top:12px;font-size:13px;line-height:20px;color:var(--muted);padding:0 12px}
.service-card .btn{position:absolute;left:50%;bottom:-20px;transform:translateX(-50%)}
.arrow-btn{position:absolute;top:436px;width:36px;height:36px;background:var(--blue);border-radius:3px;display:flex;align-items:center;justify-content:center}

/* aesthetic control */
.control{height:520px;margin-top:40px;background:var(--navy)}
.control .photo{position:absolute;left:560px;top:0;right:0;bottom:0;background:linear-gradient(135deg,#0e2a5c 0%,#2f6db3 40%,#8ab8e6 65%,#2a4f86 100%)}
.control svg.shape{position:absolute;inset:0}
.control-copy{position:absolute;left:112px;top:64px;width:440px;color:var(--white)}
.control-copy h2{font-size:32px;font-weight:800}
.control-copy h2::after{content:"";display:block;width:60px;height:4px;background:var(--blue-bright);margin-top:10px}
.control-copy ul{list-style:none;margin-top:26px}
.control-copy li{display:flex;gap:14px;font-size:14px;line-height:20px;margin-bottom:14px}
.control-copy li svg{flex:none;margin-top:2px}
.control-copy .btn{margin-top:24px;background:var(--white);color:var(--navy)}

/* awareness */
.awareness{height:660px}
.awareness .section-title{padding-top:92px;font-size:34px;line-height:44px}
.aware-cards{position:absolute;left:100px;top:258px;width:1000px;display:flex;justify-content:space-between}
.aware-card{width:300px;height:400px;background:var(--white);border-radius:6px;box-shadow:0 4px 16px rgba(12,24,56,.12);border-left:5px solid var(--blue);border-right:5px solid var(--blue);padding:30px 26px;text-align:center}
.aware-card .icon{width:74px;height:74px;margin:0 auto;background:var(--navy);border-radius:8px;display:flex;align-items:center;justify-content:center}
.aware-card:nth-child(2) .icon{background:var(--blue)}
.aware-card h3{margin-top:26px;font-size:17px;line-height:22px;font-weight:800;color:var(--navy)}
.aware-card p{margin-top:16px;font-size:13px;line-height:20px;color:var(--muted)}

/* contact */
.contact{height:580px}
.contact .section-title{padding-top:40px}
.contact-info{position:absolute;left:200px;top:148px;width:800px;display:flex;justify-content:space-between}
.info-item{display:flex;align-items:center;gap:14px}
.info-item .circle{width:54px;height:54px;border-radius:50%;background:var(--blue);display:flex;align-items:center;justify-content:center;flex:none}
.info-item b{display:block;font-size:14px;color:var(--navy)}
.info-item span{font-size:12px;line-height:17px;color:var(--muted)}
.contact-form{position:absolute;left:160px;top:250px;width:880px}
.field-row{display:flex;gap:16px}
.field{flex:1;height:46px;border:1px solid var(--line);background:var(--light);font-size:14px;color:var(--muted);padding:14px}
.field.message{margin-top:16px;height:100px}
.contact-form .btn{display:flex;width:150px;justify-content:center;margin:24px auto 0}

/* footer */
.site-footer{height:300px;background:var(--footer);color:#c7cbd6}
.footer-brand{position:absolute;left:112px;top:150px;color:var(--white);font-size:25px;line-height:30px;font-weight:800}
.footer-col{position:absolute;top:56px}
.footer-col h4{font-size:16px;font-weight:700;color:var(--white);margin-bottom:18px}
.footer-col li{list-style:none;font-size:13px;line-height:30px;display:flex;align-items:center;gap:8px}
.footer-col li::before{content:"";width:5px;height:5px;background:var(--blue-bright);border-radius:50%}
.footer-col.links{left:420px}
.footer-col.info{left:580px;width:200px}
.footer-col.info .row{display:flex;gap:10px;margin-bottom:14px;font-size:12px;line-height:17px}
.footer-col.info .row b{display:block;color:var(--white);font-size:13px}
.footer-col.news{left:806px}
.signup{display:flex;width:290px}
.signup .input{flex:1;background:var(--white);height:42px;font-size:13px;color:var(--muted);padding:13px}
.signup .go{background:var(--blue);color:var(--white);font-size:13px;font-weight:700;padding:13px 18px}
.footer-social{display:flex;gap:12px;margin-top:20px;padding-left:30px}
.footer-social span{width:36px;height:36px;border-radius:50%;background:var(--white);display:block}
.footer-social span:first-child{background:var(--blue)}
.copyright{position:absolute;left:0;top:4000px;width:1200px;height:52px;background:var(--blue);color:var(--white);font-size:13px;display:flex;align-items:center;justify-content:center}
</style>
</head>
<body>

<header class="site-header">
  <div class="brand">KESTREL FINISH<br>STUDIO</div>
  <div class="topbar">
    <div class="mail">
      <svg width="16" height="12" viewBox="0 0 16 12"><rect x="1" y="1" width="14" height="10" fill="none" stroke="#fff" stroke-width="1.5"/><path d="M1 1l7 6 7-6" fill="none" stroke="#fff" stroke-width="1.5"/></svg>
      info@kfs.com
    </div>
    <div class="phone">
      <svg width="14" height="14" viewBox="0 0 24 24"><path d="M6.6 10.8a15 15 0 006.6 6.6l2.2-2.2a1 1 0 011-.25 11.4 11.4 0 003.6.57 1 1 0 011 1V20a1 1 0 01-1 1A17 17 0 013 4a1 1 0 011-1h3.5a1 1 0 011 1c0 1.250.2 2.45.57 3.57a1 1 0 01-.25 1z" fill="#fff"/></svg>
      +1 (555) 010 2040
    </div>
  </div>
  <nav class="main-nav">
    <a class="active">HOME</a><a>ABOUT US</a><a>SERVICES</a><a>OUR PARTNERS</a><a>CONTACT US</a>
  </nav>
  <div class="social"><span></span><span></span><span></span></div>
</header>

<section class="hero">
  <div class="photo" role="img" aria-label="Person wearing a virtual reality headset inspecting a watch part"></div>
  <svg class="shape" width="1200" height="548" viewBox="0 0 1200 548">
    <polygon points="0,0 560,0 520,60 760,60 600,548 0,548" fill="#0c1838"/>
    <polygon points="520,60 760,60 740,120 500,120" fill="#1668c4"/>
    <polygon points="600,548 650,400 690,400 640,548" fill="#1668c4" opacity=".85"/>
  </svg>
  <div class="hero-text">
    <h1>KESTREL FINISH<br>STUDIO</h1>
    <p>VIRTUAL REALITY AT THE SERVICE OF CONTROLLED<br>AESTHETIC WATCHMAKING</p>
  </div>
</section>

<section class="about">
  <div class="frame">
    <div class="photo" role="img" aria-label="Screen showing a rendered golden watch component"></div>
    <div class="stand"></div>
  </div>
  <div class="about-copy">
    <h2>ABOUT KESTREL FINISH<br>STUDIO</h2>
    <p>Kestrel Finish Studio has developed in collaboration with the Brennick horology academy, a "live" simulator on a mechanical part. This allows teachers to train their students in more depth in the profession of quality controller. This tool combined with an LMS (Learning Management System) or the integrated management interface makes it possible to animate aesthetic control training in a fun and efficient way.</p>
    <span class="btn">READ MORE
      <svg width="12" height="12" viewBox="0 0 12 12"><circle cx="6" cy="6" r="6" fill="#fff"/><path d="M5 3.5L7.5 6 5 8.5" stroke="#1668c4" stroke-width="1.5" fill="none"/></svg>
    </span>
  </div>
</section>

<section class="services">
  <h2 class="section-title">OUR SERVICES</h2>
  <div class="arrow-btn" style="left:40px"><svg width="12" height="12" viewBox="0 0 12 12"><path d="M8 2L4 6l4 4" stroke="#fff" stroke-width="2" fill="none"/></svg></div>
  <div class="arrow-btn" style="left:1124px"><svg width="12" height="12" viewBox="0 0 12 12"><path d="M4 2l4 4-4 4" stroke="#fff" stroke-width="2" fill="none"/></svg></div>
  <div class="service-cards">
    <article class="service-card">
      <div class="photo" role="img" aria-label="Close-up of an open watch movement" style="background:linear-gradient(135deg,#3a2a1a,#9c7a4c 55%,#d8c8a8)"></div>
      <h3>WATCH INFORMATION</h3>
      <p>Lorem ipsum dolor sit amet consectetur adipiscing elit sed do eiusmod tempor incididunt.</p>
    </article>
    <article class="service-card featured">
      <div class="photo" role="img" aria-label="Technician reconditioning a smartphone" style="background:linear-gradient(135deg,#2b3a4e,#7f95b0 55%,#c5d0dd)"></div>
      <h3>PHONE RECONDITIONING</h3>
      <p>Lorem ipsum dolor sit amet consectetur adipiscing elit sed do eiusmod tempor incididunt.</p>
      <span class="btn">READ MORE
        <svg width="12" height="12" viewBox="0 0 12 12"><circle cx="6" cy="6" r="6" fill="#fff"/><path d="M5 3.5L7.5 6 5 8.5" stroke="#1668c4" stroke-width="1.5" fill="none"/></svg>
      </span>
    </article>
    <article class="service-card">
      <div class="photo" role="img" aria-label="Row of steel ball bearings" style="background:linear-gradient(135deg,#1b3c6e,#5d8fc8 55%,#b9d3ee)"></div>
      <h3>BALL BEARINGS</h3>
      <p>Lorem ipsum dolor sit amet consectetur adipiscing elit sed do eiusmod tempor incididunt.</p>
    </article>
  </div>
</section>

<section class="control">
  <div class="photo" role="img" aria-label="Engineer using a virtual reality headset beside a holographic car model"></div>
  <svg class="shape" width="1200" height="520" viewBox="0 0 1200 520">
    <polygon points="540,0 700,0 560,520 420,520" fill="#0c1838"/>
    <polygon points="700,0 760,0 620,520 560,520" fill="#1668c4" opacity=".9"/>
  </svg>
  <div class="control-copy">
    <h2>AESTHETIC CONTROL</h2>
    <ul>
      <li><svg width="16" height="16" viewBox="0 0 16 16"><circle cx="8" cy="8" r="8" fill="#1e88e5"/><path d="M4.5 8.2l2.4 2.3 4.6-4.8" stroke="#fff" stroke-width="1.8" fill="none"/></svg>Adopting a simple and unambiguous language for a common understanding of aesthetic quality at the extended enterprise level.</li>
      <li><svg width="16" height="16" viewBox="0 0 16 16"><circle cx="8" cy="8" r="8" fill="#1e88e5"/><path d="M4.5 8.2l2.4 2.3 4.6-4.8" stroke="#fff" stroke-width="1.8" fill="none"/></svg>Determining the compliance thresholds of the component or product.</li>
      <li><svg width="16" height="16" viewBox="0 0 16 16"><circle cx="8" cy="8" r="8" fill="#1e88e5"/><path d="M4.5 8.2l2.4 2.3 4.6-4.8" stroke="#fff" stroke-width="1.8" fill="none"/></svg>Providing uniform training in operational compliance for those responsible for aesthetic control.</li>
      <li><svg width="16" height="16" viewBox="0 0 16 16"><circle cx="8" cy="8" r="8" fill="#1e88e5"/><path d="M4.5 8.2l2.4 2.3 4.6-4.8" stroke="#fff" stroke-width="1.8" fill="none"/></svg>By designing realistic and attractive teaching sequences for total quality control.</li>
    </ul>
    <span class="btn">READ MORE
      <svg width="12" height="12" viewBox="0 0 12 12"><circle cx="6" cy="6" r="6" fill="#0c1838"/><path d="M5 3.5L7.5 6 5 8.5" stroke="#fff" stroke-width="1.5" fill="none"/></svg>
    </span>
  </div>
</section>

<section class="awareness">
  <h2 class="section-title">RAISING AWARENESS OF CRITERIA<br>AND AESTHETIC VOCABULARY</h2>
  <div class="aware-cards">
    <article class="aware-card">
      <div class="icon"><svg width="36" height="36" viewBox="0 0 36 36"><rect x="7" y="4" width="22" height="28" rx="2" fill="none" stroke="#fff" stroke-width="2.4"/><path d="M12 12h12M12 18h12M12 24h8" stroke="#fff" stroke-width="2.4"/></svg></div>
      <h3>IMPROVE AFTER-SALES<br>SERVICE RETURNS</h3>
      <p>The KFS platform can easily be used by the service network staff to assist them in the objective assessment of aesthetic defects by referring to the semantic matrix as well as to the cases already referenced.</p>
    </article>
    <article class="aware-card">
      <div class="icon"><svg width="36" height="36" viewBox="0 0 36 36"><circle cx="18" cy="14" r="9" fill="none" stroke="#fff" stroke-width="2.4"/><path d="M12 21l-3 11 9-4 9 4-3-11" fill="none" stroke="#fff" stroke-width="2.4"/></svg></div>
      <h3>IMPROVING THE TOTAL<br>QUALITY APPROACH</h3>
      <p>During the entire product life cycle, from design through customer service to distribution, the KFS application makes it possible to build up a database of aesthetic defects in a simple way.</p>
    </article>
    <article class="aware-card">
      <div class="icon"><svg width="36" height="36" viewBox="0 0 36 36"><rect x="4" y="6" width="28" height="19" rx="2" fill="none" stroke="#fff" stroke-width="2.4"/><path d="M13 31h10M18 25v6M10 12h4v4h-4zM16 12h4v4h-4zM22 12h4v4h-4z" stroke="#fff" stroke-width="2" fill="none"/></svg></div>
      <h3>A SEMANTIC MATRIX OF<br>AESTHETIC DEFECTS</h3>
      <p>KFS is based on a semantic matrix that defines 8 levels of intensity for each of the 5 types of aesthetic defects references: Scratches - Marks - Deformations - Stains - Uniformity.</p>
    </article>
  </div>
</section>

<section class="contact">
  <h2 class="section-title">CONTACT US</h2>
  <div class="contact-info">
    <div class="info-item">
      <div class="circle"><svg width="22" height="22" viewBox="0 0 24 24"><path d="M12 2a7 7 0 00-7 7c0 5 7 13 7 13s7-8 7-13a7 7 0 00-7-7zm0 9.5A2.5 2.5 0 1112 6a2.5 2.5 0 010 5.5z" fill="#fff"/></svg></div>
      <div><b>LOCATION:</b><span>27 Larkfield Row, Brennick,<br>United States</span></div>
    </div>
    <div class="info-item">
      <div class="circle"><svg width="20" height="20" viewBox="0 0 24 24"><path d="M6.6 10.8a15 15 0 006.6 6.6l2.2-2.2a1 1 0 011-.25 11.4 11.4 0 003.6.57 1 1 0 011 1V20a1 1 0 01-1 1A17 17 0 013 4a1 1 0 011-1h3.5a1 1 0 011 1c0 1.25.2 2.45.57 3.57a1 1 0 01-.25 1z" fill="#fff"/></svg></div>
      <div><b>PHONE:</b><span>+1 (555) 010 2040</span></div>
    </div>
    <div class="info-item">
      <div class="circle"><svg width="22" height="16" viewBox="0 0 16 12"><rect x="1" y="1" width="14" height="10" fill="none" stroke="#fff" stroke-width="1.5"/><path d="M1 1l7 6 7-6" fill="none" stroke="#fff" stroke-width="1.5"/></svg></div>
      <div><b>EMAIL:</b><span>info@kfs.com</span></div>
    </div>
  </div>
  <div class="contact-form">
    <div class="field-row">
      <div class="field">Full Name</div>
      <div class="field">Phone Number</div>
      <div class="field">Email Address</div>
    </div>
    <div class="field message">Message</div>
    <span class="btn">SUBMIT</span>
  </div>
</section>

<footer class="site-footer">
  <div class="footer-brand">KESTREL FINISH<br>STUDIO</div>
  <div class="footer-col links">
    <h4>QUICK LINKS</h4>
    <ul><li>Home</li><li>About Us</li><li>Services</li><li>Our Partners</li><li>Contact Us</li></ul>
  </div>
  <div class="footer-col info">
    <h4>CONTACT INFO</h4>
    <div class="row"><svg width="14" height="16" viewBox="0 0 24 24"><path d="M12 2a7 7 0 00-7 7c0 5 7 13 7 13s7-8 7-13a7 7 0 00-7-7z" fill="#1e88e5"/></svg><div><b>ADDRESS:</b>27 Larkfield Row, Brennick,<br>United States</div></div>
    <div class="row"><svg width="14" height="16" viewBox="0 0 24 24"><path d="M6.6 10.8a15 15 0 006.6 6.6l2.2-2.2a1 1 0 011-.25 11.4 11.4 0 003.6.57 1 1 0 011 1V20a1 1 0 01-1 1A17 17 0 013 4a1 1 0 011-1h3.5a1 1 0 011 1c0 1.25.2 2.45.57 3.57a1 1 0 01-.25 1z" fill="#1e88e5"/></svg><div><b>PHONE:</b>+1 (555) 010 2040</div></div>
    <div class="row"><svg width="14" height="12" viewBox="0 0 16 12"><rect x="1" y="1" width="14" height="10" fill="none" stroke="#1e88e5" stroke-width="1.5"/><path d="M1 1l7 6 7-6" fill="none" stroke="#1e88e5" stroke-width="1.5"/></svg><div><b>EMAIL:</b>info@kfs.com</div></div>
  </div>
  <div class="footer-col news">
    <h4>NEWSLETTER SIGNUP</h4>
    <div class="signup"><div class="input">Email Address</div><div class="go">SIGN UP</div></div>
    <div class="footer-social"><span></span><span></span><span></span></div>
  </div>
</footer>
<div class="copyright">© 2024 KESTREL FINISH STUDIO &nbsp;|&nbsp; All Rights Reserved</div>

</body>
</html>
```